Fern Acupuncture Business Card Design

I would like a business card design for my acupuncture business which is based from 2 practices in Melbourne, Australia.

The front of the card should include:

*The Logo
* Name - Miranda Tesselhoff (B.App.Sc.(TCM), Dip.Rem.Mass.). (I would like the letters after my name in slightly smaller font)
* Mobile number - 0472 318 604
* Web address - www.fernacupuncture.com.au

On the back of the card I would somehow like to fit my 2 clinic addresses in. They are:

The Calm & Balance Rooms
842 Pellam St, Camberwell VIC 3124
Ph: 1300 287 419

Riverbend Natural Therapies & Herbal Practice
19 Quillon Ave, Malvern East VIC 3145
Ph: (03) 9731 4052

If there is space, I'd also like to add to the back of the card - Next Appointment............................ (or something along those lines).

Thanks and happy designing!

Target Market(s)

Health consumers, and colleagues in the health industry

Industry/Entity Type

Clinic

Contact Information for Business Card

as above in brief

Requirements
Must have
• I've seen some ok designs coming in, however I'd like to avoid the generic look with the added curved line details etc. I don't particularly need extra patterns added to the card. I'd prefer it to look quite clean and simple, and using more earthy colours (I'm not super keen on the lime green that a lot of designs seem to include. I don't mind the full black or white look, (obviously the back side needs to be a lighter colour to allow me to write appointment details on it). I also quite like the idea of the background looking like brown recycled paper (just an idea - that's not 100% necessary).
Nice to have
• I have an idea that I could have the main flower part of the logo printed as metallic.
Should not have
• Generic patterns and too much added detail.

```html
<!DOCTYPE html>
<html lang="en">
<head>
<meta charset="utf-8">
<title>Fern Acupuncture – Business Card</title>
<link href="https://fonts.googleapis.com/css2?family=Cinzel:wght@400;500&family=Arimo:wght@400&display=swap" rel="stylesheet">
<style>
  :root {
    --stage: #5b5e63;
    --card-front: #fbf8f2;
    --card-back: #d9c39d;
    --ink: #3a2e22;
    --accent: #6b7440;
    --accent-back: #5a4a2c;
    --dots: #5a4a34;
  }
  * { box-sizing: border-box; margin: 0; padding: 0; }
  html, body { width: 1200px; height: 960px; overflow: hidden; }
  body {
    background: var(--stage);
    font-family: "Arimo", Arial, sans-serif;
    display: flex;
    align-items: center;
    justify-content: center;
    gap: 80px;
  }
  .card {
    position: relative;
    width: 440px;
    height: 720px;
    box-shadow: 0 10px 30px rgba(0,0,0,0.35);
    color: var(--ink);
  }

  /* Front */
  .card-front { background: var(--card-front); }
  .brand {
    position: absolute;
    top: 130px; left: 0; right: 0;
    text-align: center;
    font-family: "Cinzel", Georgia, serif;
    font-weight: 500;
    font-size: 34px;
    line-height: 1.2;
    letter-spacing: 3px;
    color: var(--accent);
  }
  .person { position: absolute; top: 380px; left: 40px; right: 24px; }
  .person-name {
    font-family: "Cinzel", Georgia, serif;
    font-weight: 400;
    font-size: 30px;
    color: var(--accent);
    letter-spacing: 1px;
    line-height: 1.1;
    white-space: nowrap;
  }
  .person-credentials { margin-top: 8px; font-size: 14px; }
  .contact-list { position: absolute; top: 480px; left: 40px; right: 24px; list-style: none; }
  .contact-item { display: flex; align-items: center; gap: 24px; font-size: 20px; margin-bottom: 26px; white-space: nowrap; }
  .contact-item svg { flex: none; width: 20px; height: 24px; }

  /* Back */
  .card-back { background: var(--card-back); }
  .appointment { position: absolute; top: 56px; left: 40px; right: 40px; }
  .appointment-label { font-size: 21px; }
  .appointment-line { border-bottom: 2px dotted var(--dots); height: 48px; }
  .appointment-line + .appointment-line { height: 40px; }
  .clinic { position: absolute; left: 84px; right: 24px; }
  .clinic-one { top: 300px; }
  .clinic-two { top: 470px; }
  .clinic-name { color: var(--accent-back); font-weight: 400; font-size: 22px; line-height: 1.25; }
  .clinic-address { font-size: 18px; margin-top: 6px; white-space: nowrap; }
  .clinic-phone { font-size: 18px; margin-top: 20px; position: relative; }
  .clinic-phone svg { position: absolute; left: -44px; top: -4px; width: 20px; height: 26px; }
</style>
</head>
<body>

<section class="card card-front" aria-label="Card front">
  <div class="brand">Fern<br>Acupuncture</div>

  <div class="person">
    <h1 class="person-name">Miranda Tesselhoff</h1>
    <p class="person-credentials">B.App.Sc.(TCM), Dip.Rem.Mass.</p>
  </div>

  <ul class="contact-list">
    <li class="contact-item">
      <svg viewBox="0 0 20 24" aria-hidden="true"><rect x="4" y="1" width="12" height="22" rx="2" fill="none" stroke="#3a2e22" stroke-width="2"/><rect x="8" y="19" width="4" height="1.5" fill="#3a2e22"/></svg>
      <span>0472 318 604</span>
    </li>
    <li class="contact-item">
      <svg viewBox="0 0 20 20" aria-hidden="true"><circle cx="10" cy="10" r="9" fill="#3a2e22"/><path d="M1 10h18M10 1c-4 4-4 14 0 18M10 1c4 4 4 14 0 18" stroke="#fbf8f2" stroke-width="1" fill="none"/></svg>
      <span>www.fernacupuncture.com.au</span>
    </li>
  </ul>
</section>

<section class="card card-back" aria-label="Card back">
  <div class="appointment">
    <p class="appointment-label">Next Appointment :-</p>
    <div class="appointment-line"></div>
    <div class="appointment-line"></div>
  </div>

  <div class="clinic clinic-one">
    <h2 class="clinic-name">The Calm &amp; Balance Rooms</h2>
    <p class="clinic-address">842 Pellam St, Camberwell VIC 3124</p>
    <p class="clinic-phone">
      <svg viewBox="0 0 22 28" aria-hidden="true"><path d="M6 2c-3 1-5 4-4 9 1 6 6 13 11 15 3 1 5 0 6-2l-4-6-3 2c-2-1-5-6-5-9l3-2z" fill="#3a2e22"/></svg>
      1300 287 419
    </p>
  </div>

  <div class="clinic clinic-two">
    <h2 class="clinic-name">Riverbend Natural Therapies &amp;<br>Herbal Practice</h2>
    <p class="clinic-address">19 Quillon Ave, Malvern East VIC 3145</p>
    <p class="clinic-phone">
      <svg viewBox="0 0 22 28" aria-hidden="true"><path d="M6 2c-3 1-5 4-4 9 1 6 6 13 11 15 3 1 5 0 6-2l-4-6-3 2c-2-1-5-6-5-9l3-2z" fill="#3a2e22"/></svg>
      (03) 9731 4052
    </p>
  </div>
</section>

</body>
</html>
```